Harvest Gateway Fellowship Ministries needs a fresh new web design

We are an up and coming multicultural church that aims to bring people into a life changing encounter with God. We need a fresh and inviting website in order to increase our internet presence and make us easier to connect with.
Here are some of the basic requirements for the site:
• Clearly displayed address, service times, and contact info
• A staff profile page
• An area for a calendar with upcoming events and their details
• Social media buttons
• Group pages for the different ministries (youth, children’s church, men, etc…)
• An area for donations and eCommerce
• A resources page for assorted media (podcasts, sermons, videos, etc.…)
• An area for prayer requests.

```html
<!DOCTYPE html>
<html lang="en">
<head>
<meta charset="utf-8">
<title>Harvest Gateway Fellowship Ministries</title>
<link href="https://fonts.googleapis.com/css2?family=Lato:wght@400;700&family=Nunito:wght@400;600;700&display=swap" rel="stylesheet">
<style>
:root{
  --orange:#e8892a;
  --orange-text:#e58a1f;
  --navy:#0b3a94;
  --blue-title:#143f8f;
  --grey-bg:#efefef;
  --grey-text:#777;
  --dark:#262626;
  --white:#fff;
}
*{margin:0;padding:0;box-sizing:border-box}
html,body{width:788px;height:1200px;overflow:hidden}
body{position:relative;font-family:'Lato',sans-serif;color:#444;
  background:linear-gradient(180deg,#c4541c 0,#d4691f 280px,#a5451a 520px,#5a3020 820px,#2b2420 1200px);}
.abs{position:absolute}
.topline{left:0;top:0;width:788px;height:4px;background:#253a8a}
.brand{left:88px;top:10px;display:flex;align-items:center;gap:6px;font-family:'Nunito',sans-serif;font-weight:700;color:var(--white);font-size:11px;line-height:1.2;width:150px}
.brand-dot{width:34px;height:34px;border-radius:50%;background:#f2c94c;flex:none}
.social{top:14px;left:586px;display:flex;gap:7px}
.social span{width:24px;height:24px;border:1.5px solid rgba(255,255,255,.8);border-radius:50%}
.contact{top:53px;left:493px;font-size:9px;color:var(--white);display:flex;gap:20px;align-items:center}
.contact div{display:flex;align-items:center;gap:6px}
.nav{left:86px;top:77px;width:616px;display:flex;gap:3px}
.nav a{flex:1;height:30px;background:#eeeeee;border-top:2px solid #ddd;text-align:center;line-height:28px;font-size:10px;color:#555;font-family:'Nunito',sans-serif;text-decoration:none}
.nav a.active{color:var(--orange-text);background:#f6f6f6}
.hero{left:87px;top:109px;width:614px;height:289px;background:linear-gradient(90deg,#c9712c 0,#e0a546 40%,#f1c461 100%)}
.hero-photo{left:0;top:0;width:300px;height:289px;background:linear-gradient(160deg,#d8903e,#7a4a2a 70%,#3a2a22)}
.hero-text{left:289px;top:85px;width:280px;color:var(--white)}
.hero-text h2{font-family:'Nunito',sans-serif;font-weight:600;font-size:22px;margin-bottom:14px}
.hero-text p{font-size:10.5px;line-height:18px}
.hero-text p.lead{line-height:14px}
.btn{display:inline-block;background:var(--navy);color:var(--white);font-family:'Nunito',sans-serif;font-weight:700;text-align:center}
.hero-btn{left:291px;top:205px;width:96px;height:30px;line-height:30px;font-size:10px}
.arrow{width:24px;height:24px}
.strip{left:87px;top:398px;width:614px;height:40px;background:var(--grey-bg)}
.strip p{position:absolute;left:14px;top:14px;font-size:7.5px;color:#555}
.strip .btn{position:absolute;left:475px;top:7px;width:134px;height:26px;line-height:26px;font-size:9.5px}
.main{left:87px;top:438px;width:614px;height:519px;background:var(--white)}
h3.title{font-family:'Nunito',sans-serif;font-weight:600;font-size:15.5px;color:var(--blue-title)}
h4.sub{font-family:'Nunito',sans-serif;font-weight:600;font-size:12px;color:var(--orange-text)}
.body-text{font-size:7.6px;line-height:13.5px;color:#555}
.muted{font-size:7.3px;line-height:13.5px;color:var(--grey-text)}
.link{font-size:8px;color:var(--navy);text-decoration:underline}
.photo{display:block}
.features{list-style:none}
.features li{font-size:8px;color:var(--orange-text);height:20.3px;display:flex;gap:8px;align-items:flex-start}
.features li::before{content:'›';color:var(--navy);font-weight:700;font-size:10px;line-height:9px}
.rule{height:1px;background:#e4e4e4}
.select{height:20px;border:1px solid #ccc;font-size:8px;color:#666;line-height:18px;padding-left:5px}
.select::after{content:'▾';position:absolute;right:0;top:0;width:18px;height:18px;background:#666;color:#fff;text-align:center}
.cal{border:1px solid #ccc;border-top:none}
.cal table{border-collapse:collapse;width:100%;font-size:8.5px;color:#999;text-align:center}
.cal th{background:#666;color:#eee;font-weight:400;font-size:7px;height:18px;border-right:1px solid #888}
.cal td{height:17px}
.cal td.today span{display:inline-block;background:var(--navy);color:#fff;width:17px;line-height:15px}
.events{background:var(--grey-bg);padding:10px 10px}
.mini-btn{width:50px;height:18px;line-height:18px;font-size:7.5px}
.banner{left:88px;top:957px;width:612px;height:35px;background:var(--navy);color:var(--white);font-family:'Nunito',sans-serif;font-size:9.5px;text-align:center;line-height:35px}
.footer{left:87px;top:992px;width:614px;height:196px;background:var(--dark);border:2px solid var(--white);border-top:none;color:#ddd}
.footer h5{font-family:'Nunito',sans-serif;font-weight:600;font-size:11.5px;color:var(--white);position:absolute;top:27px}
.hours{left:14px;top:54px;width:154px;font-size:7.5px}
.hours div{display:flex;justify-content:space-between;height:30px;line-height:20px;border-bottom:1px solid #555;padding:0 6px 0 0}
.hours div:last-child{border:none}
.loc{left:212px;top:48px;font-size:8px;line-height:15px}
.loc .row{display:flex;gap:5px;margin-bottom:10px}
.quick{left:371px;top:48px;font-size:8px;line-height:14.2px;list-style:none}
.donate-btn{left:483px;top:52px;width:115px;height:18px;border-radius:9px;background:linear-gradient(#ffd36b,#f0a424);color:#1d3b7a;font-size:9px;font-weight:700;text-align:center;line-height:18px}
.cards{left:485px;top:84px;display:flex;gap:2px}
.cards span{width:19px;height:12px;background:#ccc;border-radius:1px}
.bottom{left:14px;top:154px;width:584px;border-top:1px solid #444;padding-top:18px;display:flex;justify-content:space-between;font-size:7.5px}
.bottom .legal{color:var(--white)}
</style>
</head>
<body>
<div class="abs topline"></div>
<div class="abs brand"><span class="brand-dot"></span>Harvest Gateway<br>Fellowship Ministries</div>
<div class="abs social" aria-label="Social media links"><span></span><span></span><span></span><span></span></div>
<div class="abs contact">
  <div><svg width="11" height="8" viewBox="0 0 11 8"><rect x=".5" y=".5" width="10" height="7" fill="none" stroke="#fff"/><path d="M.5 .5 5.5 4.5 10.5 .5" fill="none" stroke="#fff"/></svg>info@harvestgateway.org</div>
  <div><svg width="10" height="10" viewBox="0 0 10 10"><circle cx="5" cy="5" r="4.3" fill="none" stroke="#fff"/><path d="M3.3 3c.3 1.8 1.7 3.3 3.4 3.7" stroke="#fff" fill="none"/></svg>555.210.4830</div>
</div>
<nav class="abs nav">
  <a class="active">HOME</a><a>ABOUT US</a><a>EVENTS</a><a>PRAYER REQUEST</a><a>DONATE</a><a>CONTACT US</a>
</nav>

<section class="abs hero">
  <div class="abs hero-photo" role="img" aria-label="Photo of a minister holding up a Bible in front of wooden crosses under a golden sky"></div>
  <div class="abs hero-text">
    <h2>RANDOM BIBLE VERSE</h2>
    <p>For all have sinned and come short of the glory of God<br>Romans 3:23</p>
    <p class="lead">Welcome to Harvest Gateway Fellowship Ministries,<br>a place where we can come together a</p>
  </div>
  <div class="abs btn hero-btn">READ MORE</div>
  <svg class="abs arrow" style="left:5px;top:132px" viewBox="0 0 24 24"><circle cx="12" cy="12" r="11" fill="none" stroke="#fff" stroke-width="1.5"/><path d="M14 7 9 12l5 5" fill="none" stroke="#fff" stroke-width="2"/></svg>
  <svg class="abs arrow" style="left:585px;top:132px" viewBox="0 0 24 24"><circle cx="12" cy="12" r="11" fill="none" stroke="#fff" stroke-width="1.5"/><path d="M10 7l5 5-5 5" fill="none" stroke="#fff" stroke-width="2"/></svg>
</section>

<div class="abs strip">
  <p>Lorem ipsum dolor sit amet, consectetuer adipiscing elit, sed diam nonummy nibh euismod tincidunt ut laoreet dolore</p>
  <div class="btn">SEND PRAYER REQUEST</div>
</div>

<main class="abs main">
  <h3 class="abs title" style="left:18px;top:14px">Welcome to HGFM</h3>
  <p class="abs body-text" style="left:18px;top:43px;width:360px">Welcome to Harvest Gateway Fellowship Ministries, a place where we can come together and fellowship. HGFM is located in Queens, New York and we would love to have you worship with us. We believe God is doing something............</p>
  <div class="abs photo" style="left:17px;top:107px;width:128px;height:106px;background:linear-gradient(180deg,#e9d3a8,#b78e5a 55%,#3c2a20)" role="img" aria-label="Silhouettes of worshippers raising hands before a cross, with a play button for a video"></div>
  <svg class="abs" style="left:68px;top:149px" width="24" height="24" viewBox="0 0 24 24"><circle cx="12" cy="12" r="10.5" fill="none" stroke="#222" stroke-width="2"/><path d="M9.5 7.5v9l7-4.5z" fill="#222"/></svg>
  <ul class="abs features" style="left:161px;top:113px">
    <li>At vero eos et accusamus et iusto odio dignissimos</li>
    <li>ducimus qui blanditiis praesentium voluptatum</li>
    <li>deleniti atque corrupti quos dolores et</li>
    <li>quas molestias excepturi sint occaecati cupiditate</li>
    <li>non provident, similique sunt in culpa</li>
  </ul>
  <div class="abs rule" style="left:18px;top:231px;width:356px"></div>
  <h3 class="abs title" style="left:18px;top:241px">Our Staffs</h3>
  <p class="abs muted" style="left:18px;top:268px;width:210px">At vero eos et accusamus et iusto odio dignissimos duci mus qui blanditiis praesentium voluptatum deleniti atq ue corrupti quos dolores et quas molestias excepturi si nt occaecati cupiditate non provident, similique sunt in culpa qui officia dese</p>
  <div class="abs link" style="left:18px;top:346px">Read More <span style="text-decoration:none">▸</span></div>
  <div class="abs photo" style="left:256px;top:256px;width:118px;height:99px;background:linear-gradient(180deg,#e6eef6,#cfdbe6)" role="img" aria-label="Portrait of a staff member holding an open Bible"></div>

  <h3 class="abs title" style="left:406px;top:14px">Church Calendar</h3>
  <div class="abs select" style="left:406px;top:47px;width:108px">March</div>
  <div class="abs select" style="left:523px;top:47px;width:76px">2014</div>
  <div class="abs cal" style="left:406px;top:80px;width:193px;height:114px">
    <table>
      <tr><th>MON</th><th>SUN</th><th>TUE</th><th>WED</th><th>THU</th><th>FRI</th><th>SAT</th></tr>
      <tr><td></td><td>01</td><td>02</td><td>03</td><td>04</td><td>05</td><td>06</td></tr>
      <tr><td>07</td><td>08</td><td>09</td><td>10</td><td>11</td><td>12</td><td>13</td></tr>
      <tr><td>14</td><td>15</td><td>16</td><td>17</td><td>18</td><td>19</td><td>20</td></tr>
      <tr><td>21</td><td>22</td><td>23</td><td class="today"><span>24</span></td><td>25</td><td>26</td><td>27</td></tr>
      <tr><td>28</td><td>29</td><td>30</td><td>31</td><td></td><td></td><td></td></tr>
    </table>
  </div>
  <div class="abs events" style="left:406px;top:208px;width:193px;height:147px">
    <h4 class="sub">Upcoming Events</h4>
    <p style="font-size:7.8px;color:#333;margin-top:9px">Ut wisi enim ad minim veniam, quis nostru</p>
    <p style="font-size:6.6px;color:#999;margin-top:4px">Time : <span style="color:#555">10.00 AM to 2.00 PM</span> Location : <span style="color:#555">Lorem</span></p>
    <p class="muted" style="font-size:6.8px;line-height:12.3px;margin-top:5px">Sed ut perspiciatis unde omnis iste natus error sit voluptatem accusantium doloremque laudantium, totam rem aperiam, eaque ipsa quae ab illo inventore veritatis et quasi......</p>
    <div class="link" style="margin-top:8px">Read More <span style="text-decoration:none">▸</span></div>
  </div>

  <div class="abs rule" style="left:18px;top:376px;width:581px"></div>
  <div class="abs photo" style="left:17px;top:397px;width:116px;height:91px;background:linear-gradient(180deg,#9fb07a,#c9b9a6 55%,#e7e1d6)" role="img" aria-label="Group of young people praying together on the grass"></div>
  <h4 class="abs sub" style="left:145px;top:401px">Our Vision</h4>
  <p class="abs muted" style="left:145px;top:419px;width:150px">At vero eos et accusamus et iusto odio mus qui blanditiis praesentium volup ue corrupti quos dolores et quas mo nt occaecati cupiditate.......</p>
  <div class="abs btn mini-btn" style="left:146px;top:472px">MORE</div>
  <div class="abs" style="left:307px;top:402px;width:1px;height:70px;background:#e4e4e4"></div>
  <div class="abs photo" style="left:328px;top:397px;width:115px;height:91px;background:radial-gradient(circle at 50% 45%,#fff3c8,#e9c770 50%,#c99a40)" role="img" aria-label="Ministry emblem artwork on a golden background"></div>
  <h4 class="abs sub" style="left:455px;top:401px">Our History</h4>
  <p class="abs muted" style="left:455px;top:419px;width:150px">At vero eos et accusamus et iusto odio mus qui blanditiis praesentium volup ue corrupti quos dolores et quas mo nt occaecati cupiditate.......</p>
  <div class="abs btn mini-btn" style="left:457px;top:472px">MORE</div>
</main>

<div class="abs banner">"NO LIMITS, NO BOUNDARIES, BUT INCREASE IN JESUS NAME"</div>

<footer class="abs footer">
  <h5 style="left:14px">Service Times</h5>
  <div class="abs hours">
    <div><span>MON - FRI</span><span>10.00 AM to 3.00PM</span></div>
    <div><span>SAT</span><span>9.00 AM to 4.00PM</span></div>
    <div><span>SUN</span><span>9.00 AM to 6.00PM</span></div>
  </div>
  <h5 style="left:212px">Our Location</h5>
  <div class="abs loc">
    <div class="row"><svg width="9" height="12" viewBox="0 0 9 12"><path d="M4.5 11.5S.5 6.8.5 4.3a4 4 0 0 1 8 0c0 2.5-4 7.2-4 7.2z" fill="#ddd"/><circle cx="4.5" cy="4.3" r="1.5" fill="#262626"/></svg><span>Lorem Ipsm, Lorem Ipsm<br>Lorem Ipsm - 123 456</span></div>
    <div class="row"><svg width="10" height="10" viewBox="0 0 10 10"><path d="M2 1l2 2-1 1.3c.6 1.3 1.4 2.1 2.7 2.7L7 6l2 2-1.3 1.5C4.5 9.2.8 5.5.5 2.3z" fill="#ddd"/></svg><span>555.210.4830</span></div>
    <div class="row"><svg width="11" height="9" viewBox="0 0 11 9"><rect x=".5" y=".5" width="10" height="8" fill="none" stroke="#ddd"/><path d="M.5 .5l5 4 5-4" fill="none" stroke="#ddd"/></svg><span>info@harvestgateway.org</span></div>
  </div>
  <h5 style="left:371px">Quick Links</h5>
  <ul class="abs quick">
    <li>Home</li><li>About Us</li><li>Events</li><li>Our Services</li><li>Upcoming Events</li><li>Prayer Request</li>
  </ul>
  <h5 style="left:483px">Donate</h5>
  <div class="abs donate-btn">Donate Online</div>
  <div class="abs cards" aria-label="Accepted payment cards"><span></span><span></span><span></span><span></span><span></span></div>
  <div class="abs bottom">
    <span>© 2014 HGFM. All Rights Reserved</span>
    <span class="legal">Privacy Policy | Terms Conditions | Sitemap | Contact Us</span>
  </div>
</footer>
</body>
</html>
```